corvale institute of business and technology web site

I need web site for the institute which focus on business courses and computer course it is also for vocation train for employment It is also carear development and advancement .It should have links to online study resource which free
Industry/Entity Type
Business
Number of Pages Required
1 page
Look and feel
Each slider illustrates characteristics of the customer's brand and the style your logo design should communicate.

```html
<!DOCTYPE html>
<html lang="en">
<head>
<meta charset="utf-8">
<title>Corvale Institute of Business and Technology</title>
<link href="https://fonts.googleapis.com/css2?family=Open+Sans:wght@300;400;600;700&display=swap" rel="stylesheet">
<style>
:root{
  --blue:#1f8bd3;
  --blue-dark:#146fae;
  --blue-light:#dcecf8;
  --orange:#f5a21b;
  --ink:#333c44;
  --muted:#6d7780;
  --page:#f1f2f3;
  --card:#e8ebed;
  --band:#e3e6e8;
  --footer:#2d3640;
  --footer-deep:#232a32;
  --white:#ffffff;
}
*{box-sizing:border-box;margin:0;padding:0}
html,body{width:691px;height:1200px;overflow:hidden}
body{font-family:"Open Sans",Arial,sans-serif;background:var(--page);color:var(--ink);position:relative}
.site-header{position:absolute;top:0;left:0;width:691px;height:80px;background:linear-gradient(180deg,#2a9ae0,var(--blue-dark))}
.brand{position:absolute;left:24px;top:14px;display:flex;align-items:center;gap:8px;color:var(--white);font-weight:700;line-height:1.15}
.brand-mark{width:26px;height:30px;background:var(--white);border-radius:3px}
.brand-name{font-size:12px;letter-spacing:.3px}
.brand-name span{display:block;font-size:9.5px}
.social{position:absolute;display:flex;gap:5px}
.social i{display:block;width:17px;height:17px;border-radius:50%;border:1.5px solid var(--white)}
.site-header .social{right:26px;top:12px}
.main-nav{position:absolute;right:26px;top:56px;display:flex;gap:16px}
.main-nav a{color:var(--white);font-size:9px;font-weight:700;text-decoration:none}
.hero{position:absolute;top:80px;left:0;width:691px;height:300px;background:radial-gradient(ellipse at 55% 40%,#f4f9fd 0%,#bcdaf1 45%,#5d9fd3 100%)}
.slider-arrow{position:absolute;top:140px;width:20px;height:20px;border-radius:50%;background:#2b3640}
.slider-arrow.prev{left:16px}.slider-arrow.next{right:16px}
.slider-arrow svg{width:20px;height:20px}
.content{position:absolute;top:380px;left:0;width:691px;height:515px;background:var(--white)}
.welcome{position:absolute;left:30px;top:20px;width:400px}
.welcome h1{color:var(--blue);font-size:13px;font-weight:700;line-height:1.3;margin-bottom:10px}
.welcome p{font-size:7.6px;line-height:11px;color:var(--muted)}
.featured{position:absolute;left:452px;top:16px;width:210px}
.section-title{font-size:11px;font-weight:700;color:var(--ink);padding-bottom:6px;border-bottom:2px solid #d5d9dc;margin-bottom:8px}
.video-thumb{position:relative;height:112px;background:linear-gradient(135deg,#4f6b84,#9fb8cc 60%,#d7e2ea)}
.play{position:absolute;left:88px;top:38px;width:34px;height:34px}
.featured p{font-size:7.6px;color:var(--muted);margin-top:5px;line-height:10px}
.programs{position:absolute;left:30px;top:222px;width:631px}
.program-arrows{position:absolute;right:0;top:0;display:flex;gap:8px}
.program-arrows svg{width:10px;height:12px}
.cards{display:flex;gap:10px}
.card{position:relative;width:150px;height:180px;background:var(--card);padding:8px}
.card h3{font-size:8.4px;font-weight:700;line-height:11px;height:24px;color:var(--ink)}
.card-image{height:72px;margin:4px 0 8px}
.card p{font-size:7.4px;line-height:10px;color:var(--muted)}
.card .corner{position:absolute;right:0;bottom:0;width:0;height:0;border-left:16px solid transparent;border-bottom:16px solid var(--blue)}
.study-banner{position:absolute;left:30px;top:455px;width:631px;height:44px;border-top:1px solid #d8dcdf;display:flex;align-items:center;justify-content:center;gap:28px;padding-top:8px}
.study-banner h2{font-size:21px;font-weight:300;color:#4a545d;letter-spacing:.3px}
.study-banner h2 strong{color:var(--orange);font-weight:700}
.btn{display:inline-block;background:var(--orange);color:var(--white);font-weight:700;text-decoration:none;border-radius:12px}
.study-banner .btn{font-size:10px;padding:6px 22px}
.newsletter{position:absolute;top:895px;left:0;width:691px;height:58px;background:var(--band)}
.newsletter-label{position:absolute;left:34px;top:14px;display:flex;align-items:center;gap:8px;font-size:10px;font-weight:700;color:#4a545d;line-height:1.1}
.newsletter-label svg{width:26px;height:20px}
.news-input{position:absolute;left:196px;top:20px;width:150px;height:18px;background:var(--white);border:1px solid #cfd4d8;font-size:7px;color:#999;padding:4px 6px}
.newsletter .btn{position:absolute;left:352px;top:20px;height:18px;border-radius:2px;font-size:7.5px;padding:4px 10px}
.newsletter .social{right:26px;top:20px}
.newsletter .social i{border-color:#5b656e}
.site-footer{position:absolute;top:953px;left:0;width:691px;height:227px;background:var(--footer);padding:20px 30px;display:flex;gap:18px}
.footer-col{flex:1;color:#b8c0c7;font-size:7.4px;line-height:11px}
.footer-col h4{color:var(--white);font-size:8.5px;font-weight:700;margin-bottom:8px}
.footer-col li{list-style:none}
.news-item{margin-bottom:8px}
.news-item time{display:block;color:var(--orange);font-size:7px}
.contact-line{display:flex;align-items:center;gap:6px;margin-bottom:7px}
.contact-line svg{width:10px;height:10px;flex:none}
.copyright{position:absolute;top:1180px;left:0;width:691px;height:20px;background:var(--footer-deep);color:#8a949c;font-size:6.8px;text-align:center;line-height:20px}
</style>
</head>
<body>
<header class="site-header">
  <div class="brand"><div class="brand-mark"></div><div class="brand-name">CORVALE<span>INSTITUTE OF BUSINESS &amp; TECHNOLOGY</span></div></div>
  <div class="social"><i></i><i></i><i></i><i></i></div>
  <nav class="main-nav"><a href="#">HOME</a><a href="#">ABOUT US</a><a href="#">COURSES</a><a href="#">CONTACT US</a></nav>
</header>

<section class="hero" role="img" aria-label="Slider photo: student working with floating digital interface screens">
  <span class="slider-arrow prev"><svg viewBox="0 0 20 20"><path d="M12 6l-4 4 4 4" stroke="#fff" stroke-width="2" fill="none"/></svg></span>
  <span class="slider-arrow next"><svg viewBox="0 0 20 20"><path d="M8 6l4 4-4 4" stroke="#fff" stroke-width="2" fill="none"/></svg></span>
</section>

<main class="content">
  <section class="welcome">
    <h1>WELCOME TO<br>CORVALE INSTITUTE OF BUSINESS AND TECHNOLOGY</h1>
    <p>Corvale Institute of Business and Technology (CIBT) is a fast growing Education &amp; Training Solution Provider, focusing on holistic knowledge and skills intermediate that impact livelihoods. It is established on the core values of making a meaningful and measurable difference on career aspirations and goals through innovative learning and knowledge management interventions. CIBT prepares students not only for professional careers but also inculcates the larger sense of discipline and equips them physically, mentally, socially and spiritually. The institution is licensed and registered under the National Vocational Training Authority (NVTA).</p>
  </section>

  <aside class="featured">
    <h2 class="section-title">FEATURED VIDEO</h2>
    <div class="video-thumb" role="img" aria-label="Video still of a presenter at a lecture">
      <svg class="play" viewBox="0 0 34 34"><circle cx="17" cy="17" r="17" fill="#1f8bd3"/><path d="M13 10l11 7-11 7z" fill="#fff"/></svg>
    </div>
    <p>Lorem ipsum dolor sit amet, consectetur adipiscing elit.</p>
  </aside>

  <section class="programs">
    <h2 class="section-title">PROGRAMS OFFERED</h2>
    <div class="program-arrows">
      <svg viewBox="0 0 10 12"><path d="M8 1L2 6l6 5" stroke="#555" stroke-width="2" fill="none"/></svg>
      <svg viewBox="0 0 10 12"><path d="M2 1l6 5-6 5" stroke="#555" stroke-width="2" fill="none"/></svg>
    </div>
    <div class="cards">
      <article class="card"><h3>University Education – Long Distance Learning</h3><div class="card-image" role="img" aria-label="Photo of graduates in gowns" style="background:linear-gradient(135deg,#2d3a4a,#7f8fa0)"></div><p>Lorem ipsum dolor sit amet, consectetur adipiscing elit, sed do eiusmod tempor incididunt ut labore et dolore magna aliqua. Ut enim ad minim.</p><span class="corner"></span></article>
      <article class="card"><h3>Modular Soft Skills</h3><div class="card-image" role="img" aria-label="Photo of a training workshop" style="background:linear-gradient(135deg,#8a9aa6,#d4dbe0)"></div><p>Lorem ipsum dolor sit amet, consectetur adipiscing elit, sed do eiusmod tempor incididunt ut labore et dolore magna aliqua. Ut enim ad minim.</p><span class="corner"></span></article>
      <article class="card"><h3>Direct to Device (D2D)</h3><div class="card-image" role="img" aria-label="Photo of a tablet and mobile devices" style="background:linear-gradient(135deg,#4d88c4,#b9d6ee)"></div><p>Lorem ipsum dolor sit amet, consectetur adipiscing elit, sed do eiusmod tempor incididunt ut labore et dolore magna aliqua. Ut enim ad minim.</p><span class="corner"></span></article>
      <article class="card"><h3>Teleskill</h3><div class="card-image" role="img" aria-label="Photo of a telecom tower" style="background:linear-gradient(180deg,#9ec7e8,#5d7d95)"></div><p>Lorem ipsum dolor sit amet, consectetur adipiscing elit, sed do eiusmod tempor incididunt ut labore et dolore magna aliqua. Ut enim ad minim.</p><span class="corner"></span></article>
    </div>
  </section>

  <section class="study-banner">
    <h2>ONLINE STUDY RESOURCE WHICH <strong>FREE</strong></h2>
    <a class="btn" href="#">CLICK HERE</a>
  </section>
</main>

<section class="newsletter">
  <div class="newsletter-label">
    <svg viewBox="0 0 26 20"><rect x="1" y="3" width="20" height="14" fill="none" stroke="#4a545d" stroke-width="1.5"/><path d="M1 3l10 8 10-8" fill="none" stroke="#4a545d" stroke-width="1.5"/></svg>
    <span>SUBSCRIBE<br>OUR NEWSLETTER</span>
  </div>
  <div class="news-input">Enter Your Email</div>
  <a class="btn" href="#">SUBSCRIBE</a>
  <div class="social"><i></i><i></i><i></i><i></i></div>
</section>

<footer class="site-footer">
  <div class="footer-col"><h4>NAVIGATION</h4><ul><li>Home</li><li>About Us</li><li>Courses</li><li>Contact Us</li></ul></div>
  <div class="footer-col"><h4>PROGRAMS OFFERED</h4><ul><li>University Education – Long Distance Learning</li><li>Modular Soft Skills</li><li>Direct to Device (D2D)</li><li>Teleskill</li><li>Technology Water &amp; Client Connection</li><li>Business Outlook</li><li>Technology Capabilities</li></ul></div>
  <div class="footer-col"><h4>RECENT NEWS</h4>
    <div class="news-item"><time>January 12, 2015</time>Lorem ipsum dolor sit amet, consectetur adipiscing elit.</div>
    <div class="news-item"><time>January 08, 2015</time>Lorem ipsum dolor sit amet, consectetur adipiscing elit.</div>
  </div>
  <div class="footer-col"><h4>CONTACT INFO</h4>
    <div class="contact-line"><svg viewBox="0 0 10 10"><path d="M5 0a3.5 3.5 0 0 0-3.5 3.5C1.5 6 5 10 5 10s3.5-4 3.5-6.5A3.5 3.5 0 0 0 5 0z" fill="#b8c0c7"/></svg>42 Harbour Lane, Westfield 10230</div>
    <div class="contact-line"><svg viewBox="0 0 10 10"><path d="M2 0l2 2-1 1.5a6 6 0 0 0 3.5 3.5L8 6l2 2-1.5 2C4 10 0 6 0 1.5z" fill="#b8c0c7"/></svg>Phone: +1 555 0142 300</div>
    <div class="contact-line"><svg viewBox="0 0 10 10"><rect x="0" y="2" width="10" height="7" fill="none" stroke="#b8c0c7"/><path d="M0 2l5 4 5-4" fill="none" stroke="#b8c0c7"/></svg>Email: info@corvale.edu</div>
  </div>
</footer>
<div class="copyright">© 2015 Corvale Institute of Business and Technology. All Rights Reserved.</div>
</body>
</html>
```